BRISK requires an exciting new business card

New business card required for BRISK. We are a new market research consultancy and want our brand to be approachable and be contemporary/modern, bold, uncomplicated/simple, and use friendly and easy to read fonts.

A draft website front page is attached to give you a feel (the pictures will be improved over the coming days).

The business card will be printed on 600gsm card, full colour both sides. The card is unique in that it allows one of four colours to be placed within the seam of the card (see http://uk.prentvo.com/products/gilt/business-cards.html)

The logo has been designed in yellow on white, white on yellow, yellow on black and black on yellow - please select whichever you feel most appropriate from the attached document (please use the versions with the tagline). I think my preference is yellow on white for the front, and then yellow or black as the dominant colour on the back.

Telephone numbers will be given next week as they are now being finalised.

Thanks

Target Market(s)

Professionals in large corporates, such as Marketing Managers at Grovane, Fizzaro Pop, Delmarco etc.

Industry/Entity Type

Market Research

Requirements
Must have
• Dana Pruitt QPMR
brisk
Level 4, 37 Quarrell St
Surrey Hills
NSW 2010
Tel: 02 XXXX XXXX
Mob: XXXX XXXXXX
Email: dana@briskqr.com.au
Web: www.briskqr.com.au

```html
<!DOCTYPE html>
<html lang="en">
<head>
<meta charset="utf-8">
<title>BRISK business card</title>
<link rel="stylesheet" href="https://fonts.googleapis.com/css2?family=Source+Sans+3:ital,wght@0,400;0,600;0,700;1,400;1,700&display=swap">
<style>
  :root {
    --brand-yellow: #fcc90a;
    --brand-charcoal: #414142;
    --card-white: #ffffff;
    --backdrop: #e9e6e1;
    --label-ink: #1d1d1d;
    --text-ink: #2b2b2b;
  }
  * { box-sizing: border-box; margin: 0; padding: 0; }
  html, body {
    width: 1200px; height: 788px; overflow: hidden;
    background: var(--backdrop);
    font-family: "Source Sans 3", Arial, sans-serif;
  }
  .sheet { position: relative; width: 1200px; height: 788px; }

  .view-label {
    position: absolute; width: 300px; text-align: center;
    font-size: 22px; font-weight: 400; color: var(--label-ink);
  }

  .card {
    position: absolute; width: 525px; height: 300px;
    border-radius: 22px; overflow: hidden;
    box-shadow: 0 6px 14px rgba(0,0,0,.25);
  }
  .card--white { background: var(--card-white); }
  .card--charcoal { background: var(--brand-charcoal); }
  .card--yellow { background: var(--brand-yellow); }

  .card-edge-band {
    position: absolute; left: 0; right: 0; bottom: 0; height: 7px;
    background: var(--brand-yellow);
  }

  .brand-name {
    position: absolute; left: 0; right: 0; text-align: center;
    font-weight: 600; line-height: 1; letter-spacing: -1px;
  }
  .brand-name--front { top: 38px; font-size: 88px; color: var(--brand-yellow); }
  .brand-name--back { top: 78px; font-size: 136px; }
  .ink-charcoal .brand-name { color: var(--brand-charcoal); }
  .ink-yellow .brand-name { color: var(--brand-yellow); }

  .holder {
    position: absolute; top: 172px; left: 0; right: 0; text-align: center;
    font-size: 17px; font-weight: 700; color: var(--text-ink);
  }
  .holder-credential { font-size: 12px; font-style: italic; font-weight: 400; }

  .contact {
    position: absolute; top: 205px; left: 0; right: 0;
    display: flex; justify-content: center;
    font-size: 13px; color: var(--text-ink); line-height: 20px;
  }
  .contact-column { padding: 0 10px; }
  .contact-column--phones { text-align: right; border-right: 1px solid #555; }
  .contact-column--online { text-align: left; }
  .contact-key { font-weight: 700; font-style: italic; }

  .address {
    position: absolute; top: 258px; left: 0; right: 0; text-align: center;
    font-size: 13px; color: var(--text-ink);
  }
</style>
</head>
<body>
<main class="sheet">
  <p class="view-label" style="left:170px; top:33px;">Front</p>
  <p class="view-label" style="left:745px; top:33px;">Back - 1</p>
  <p class="view-label" style="left:170px; top:403px;">Back - 2</p>
  <p class="view-label" style="left:745px; top:403px;">Back - 3</p>

  <section class="card card--white" style="left:53px; top:74px;" aria-label="Card front">
    <span class="card-edge-band" aria-hidden="true"></span>
    <p class="brand-name brand-name--front">brisk</p>
    <p class="holder">Dana Pruitt - <span class="holder-credential">QPMR</span></p>
    <div class="contact">
      <div class="contact-column contact-column--phones">
        <div><span class="contact-key">p</span> : 02 XXXX XXXX</div>
        <div><span class="contact-key">c</span> : XXXX XXXXXX</div>
      </div>
      <div class="contact-column contact-column--online">
        <div><span class="contact-key">e</span> : dana@briskqr.com.au</div>
        <div><span class="contact-key">w</span> : www.briskqr.com.au</div>
      </div>
    </div>
    <p class="address">brisk Level 4, 37 Quarrell St, Dunmore Vale, NSW 2094</p>
  </section>

  <section class="card card--white ink-charcoal" style="left:622px; top:74px;" aria-label="Card back, white">
    <p class="brand-name brand-name--back">brisk</p>
  </section>

  <section class="card card--charcoal ink-yellow" style="left:53px; top:445px;" aria-label="Card back, charcoal">
    <p class="brand-name brand-name--back">brisk</p>
  </section>

  <section class="card card--yellow ink-charcoal" style="left:622px; top:440px;" aria-label="Card back, yellow">
    <p class="brand-name brand-name--back">brisk</p>
  </section>
</main>
</body>
</html>
```